Digital Book Cover

I am currently in the process of building a digital book for my web site but struggling with the front and back covers. We are an ecommerce business selling notice boards of all kind, indoor, outdoor, hospitality, staff boards, whiteboards, mobile and so on.

The company web site is orange and white. We already have a company logo which we would like included. The logo is simply the word "larchwick" in black and the work "company" in orange. When our web site was redesigned the company that designed it reversed the colours of the logo and had the word "larchwick" in black & "company" in white onto an orange banner. Either way I don't mind.

Target Market(s)

We sell to everyone online including schools colleges, universities, KTB, companies, churches, supermarkets, hotels etc. If fact everyone!

Industry/Entity Type

Digital

Requirements
Must have
• Company colours and include the company logo and strap line "A Larchwick For Every Location"
• Company details including postal address, phone, fax, email and web site.
• Finish cover to be supplied as a PDF

```html
<!DOCTYPE html>
<html lang="en">
<head>
<meta charset="utf-8">
<title>Larchwick Company – Back Cover</title>
<link rel="stylesheet" href="https://fonts.googleapis.com/css2?family=Arimo:wght@400&display=swap">
<style>
  :root {
    --orange-deep: #e6a216;
    --orange-mid: #f0ae1e;
    --orange-light: #f6be3a;
    --orange-pale: #f8d27e;
    --ink: #1a1408;
    --paper: #ffffff;
  }
  html, body {
    margin: 0;
    padding: 0;
    overflow: hidden;
    background: var(--paper);
  }
  .cover {
    position: relative;
    width: 848px;
    height: 1200px;
    overflow: hidden;
    background: linear-gradient(160deg, var(--orange-deep) 0%, var(--orange-mid) 55%, var(--orange-light) 100%);
    font-family: "Arimo", Arial, sans-serif;
  }
  .cover__artwork {
    position: absolute;
    inset: 0;
    background:
      radial-gradient(ellipse 70% 45% at 35% 28%, var(--orange-pale) 0%, rgba(246, 190, 58, 0.55) 45%, rgba(240, 174, 30, 0) 100%);
  }
  .contact {
    position: absolute;
    left: 70px;
    top: 0;
    width: 760px;
  }
  .contact__line {
    position: absolute;
    left: 0;
    margin: 0;
    white-space: nowrap;
    line-height: 1;
    font-weight: 400;
  }
  .contact__company { top: 766px; font-size: 45px; color: var(--ink); }
  .contact__street  { top: 838px; font-size: 49px; color: var(--paper); }
  .contact__town    { top: 909px; font-size: 39px; color: var(--paper); }
  .contact__phone   { top: 1001px; font-size: 33px; color: var(--paper); }
  .contact__email   { top: 1055px; font-size: 37px; color: var(--ink); }
  .contact__web     { top: 1110px; font-size: 39px; color: var(--ink); }
</style>
</head>
<body>
<main class="cover">
  <div class="cover__artwork" role="img" aria-label="Glossy orange sphere with a broad white highlight arc across the top"></div>

  <section class="contact">
    <p class="contact__line contact__company">Larchwick Company (UK) Ltd</p>
    <p class="contact__line contact__street">Harlow House - PO Box 4120</p>
    <p class="contact__line contact__town">Bramford - East Vale - BV4 2QT</p>
    <p class="contact__line contact__phone">Phone: 01632 960418 - Fax: 01632 960527</p>
    <p class="contact__line contact__email">Email: sales@larchwickcompany.com</p>
    <p class="contact__line contact__web">Web: www.larchwickcompany.com</p>
  </section>
</main>
</body>
</html>
```